Harborline Renewal Business Card Design

Professional and clean design. The design colors should flow with the logo. Two-sided card with the website on the back which is:

www.HarborlineRenewal.example.

"Specializing in Water Damage Restoration"

On the front I need the name, email, phone, and logo.

Name: Darnell Quisby
Email: Darnell@HarborlineRenewal.example
Phone: 555-318-2046 for now

I only have the Preview and Thumbnail right now but should have the source files uploaded within a day or two.

Target Market(s)

Flood victims, home owners with water damage from busted pipes etc...

Industry/Entity Type

Business

Contact Information for Business Card

Name: Darnell Quisby

Font styles to use
Serif
Sans Serif

Requirements
Must have
• Business Card Details Info

```html
<!DOCTYPE html>
<html lang="en">
<head>
<meta charset="utf-8">
<title>Harborline Renewal Business Card</title>
<link rel="stylesheet" href="https://fonts.googleapis.com/css2?family=Cinzel:wght@500&family=Open+Sans:wght@400;700&display=swap">
<style>
  :root {
    --brand-blue: #2899d6;
    --brand-blue-light: #5bbde9;
    --ink-white: #ffffff;
    --card-white: #ffffff;
    --wash: #eef5fb;
    --backdrop: #1c1c1c;
  }
  html, body {
    margin: 0;
    padding: 0;
    overflow: hidden;
  }
  .canvas {
    position: relative;
    width: 1200px;
    height: 741px;
    background: var(--backdrop);
    overflow: hidden;
  }
  .card {
    position: absolute;
    top: 236px;
    width: 495px;
    height: 282px;
    overflow: hidden;
  }
  /* Back side */
  .card-back {
    left: 86px;
    background: var(--brand-blue);
    color: var(--ink-white);
  }
  .card-back .mark-circle {
    position: absolute;
    left: 213px;
    top: 56px;
    width: 70px;
    height: 70px;
    border-radius: 50%;
    background: var(--ink-white);
  }
  .card-back .brand-name {
    position: absolute;
    left: 0;
    right: 0;
    top: 143px;
    text-align: center;
    font: 500 26px/1 "Cinzel", serif;
    letter-spacing: 1px;
  }
  .card-back .tagline {
    position: absolute;
    left: 0;
    right: 0;
    top: 184px;
    text-align: center;
    font: 400 12.5px/1 "Open Sans", sans-serif;
  }
  .card-back .web-row {
    position: absolute;
    left: 0;
    right: 0;
    top: 241px;
    display: flex;
    align-items: center;
    font: 400 12.5px/1 "Open Sans", sans-serif;
  }
  .card-back .web-row .rule {
    height: 1px;
    background: var(--ink-white);
    flex: 1;
  }
  .card-back .web-row .rule-left { flex: 0 0 138px; }
  .card-back .web-row .rule-right { flex: 0 0 136px; }
  .card-back .web-row .url {
    flex: 1;
    text-align: center;
  }
  /* Front side */
  .card-front {
    left: 618px;
    background: var(--card-white);
  }
  .card-front .side-band {
    position: absolute;
    left: 0;
    top: 0;
    bottom: 0;
    width: 74px;
    background: var(--brand-blue);
  }
  .card-front .side-line {
    position: absolute;
    left: 76px;
    top: 0;
    bottom: 0;
    width: 2px;
    background: var(--brand-blue);
  }
  .card-front .faint-circle {
    position: absolute;
    left: 310px;
    top: 26px;
    width: 230px;
    height: 230px;
    border-radius: 50%;
    background: var(--wash);
  }
  .card-front .mark-circle {
    position: absolute;
    left: 33px;
    top: 28px;
    width: 74px;
    height: 74px;
    border-radius: 50%;
    background: var(--card-white);
    border: 4px solid var(--brand-blue);
    box-sizing: border-box;
  }
  .card-front .brand-name {
    position: absolute;
    left: 135px;
    top: 46px;
    font: 500 24px/1 "Cinzel", serif;
    color: var(--brand-blue);
    letter-spacing: 0.5px;
  }
  .card-front .person-name {
    position: absolute;
    left: 135px;
    top: 154px;
    font: 700 19px/1 "Open Sans", sans-serif;
    color: var(--brand-blue);
  }
  .contact-list {
    position: absolute;
    left: 135px;
    top: 200px;
    margin: 0;
    padding: 0;
    list-style: none;
    font: 400 13.5px/18px "Open Sans", sans-serif;
    color: var(--brand-blue);
  }
  .contact-list li {
    display: flex;
    align-items: center;
    gap: 6px;
  }
  .contact-list svg {
    width: 13px;
    height: 13px;
    flex: none;
  }
</style>
</head>
<body>
<div class="canvas">

  <section class="card card-back" aria-label="Card back">
    <div class="mark-circle"></div>
    <div class="brand-name">Harborline Renewal</div>
    <div class="tagline">Specializing in Water Damage Restoration</div>
    <div class="web-row">
      <span class="rule rule-left"></span>
      <span class="url">www.HarborlineRenewal.example</span>
      <span class="rule rule-right"></span>
    </div>
  </section>

  <section class="card card-front" aria-label="Card front">
    <div class="faint-circle"></div>
    <div class="side-band"></div>
    <div class="side-line"></div>
    <div class="mark-circle"></div>
    <div class="brand-name">Harborline Renewal</div>
    <div class="person-name">Darnell Quisby</div>
    <ul class="contact-list">
      <li>
        <svg viewBox="0 0 13 13" aria-hidden="true">
          <rect width="13" height="13" fill="#5bbde9"/>
          <path d="M3 4.5c0-1 1-1.5 3.5-1.5S10 3.5 10 4.5v1H8.5V4.5h-4v1H3z M4 6.5h5l1 3H3z" fill="#fff"/>
        </svg>
        <span>555-318-2046</span>
      </li>
      <li>
        <svg viewBox="0 0 13 13" aria-hidden="true">
          <rect width="13" height="13" fill="#5bbde9"/>
          <rect x="2.5" y="3.5" width="8" height="6" fill="none" stroke="#fff"/>
          <path d="M2.5 3.5l4 3.5 4-3.5" fill="none" stroke="#fff"/>
        </svg>
        <span>Darnell@HarborlineRenewal.example</span>
      </li>
      <li>
        <svg viewBox="0 0 13 13" aria-hidden="true">
          <rect width="13" height="13" fill="#5bbde9"/>
          <circle cx="6.5" cy="6.5" r="4" fill="none" stroke="#fff"/>
          <path d="M2.5 6.5h8 M6.5 2.5v8" stroke="#fff"/>
        </svg>
        <span>www.HarborlineRenewal.example</span>
      </li>
    </ul>
  </section>

</div>
</body>
</html>
```